Flyer Vacation Gift Certificate

I need to create a beautiful flyer 8.5 x 11 PDF format flyer design. <br/><br/>Instructions:<br/>The flyer will really be a gift voucher for a las vegas vacation getaway. So must have a Las Vegas Theme exciting fun<br/><br/>The voucher should have two modules that will be editable. <br/>Must have a "Compliments Of" area and also must have an "Exclusively For" area<br/><br/>Keep in mind that this flyer will be printed so keep that in mind :)<br/><br/>Here the is the content for the vacation voucher:<br/><br/>There is no doubt that Las Vegas is one of the hottest travel destinations around the world. In fact, some people would even go as far as<br/>saying that perhaps it is THE hottest place to visit. Enjoy up to 4 nights of resort/casino accommodations in exciting Las Vegas, NV. Millions of people travel to this exciting city each year to enjoy its thrills. Thanks to the business you received this certificate from, now you can enjoy exciting Las Vegas, NV too!<br/><br/>Features:<br/>*Travel 7 Days A Week<br/>*Stay Your Choice Of Nights (1-4 Nights)<br/>*Good For Two Adults & Two Children<br/>*Pay Just The Taxes & Fees<br/>*Multiple Travel Date Requests Allowed<br/>*Fully Transferable To Another Person<br/>*Just A 30 Days Advance Notice Required<br/>*You Will Have 12 Months To Complete Travel After Redemption<br/><br/>HOW CAN WE DO THIS?<br/><br/>We contract with the world leading hotel chains and resorts to help them fill their otherwise empty rooms.<br/><br/>We help fill empty rooms which the hotels, resorts and cruise lines turn into additional revenue from other areas of their property and future bookings.<br/><br/>Hotels rarely experience full occupancy, yet they remain open, providing rooms and services at fixed costs. So when hotels give out their rooms by partnering with marketing companies like us, they might miss out on the room fee, but they already didn't have that in the first place, at least now they have the opportunity to gain a customer for their in-house restaurants, room service, their casinos, an extra day stay, future bookings, etc.<br/><br/>VIEW ALL THE DETAILS OF THIS SPECIAL OFFER AND REDEEM ONLINE AT <br/>WWW.QOTAVERNIX.COM<br/><br/>Certificate ID # 47261-38157<br/>Expires 02/29/2020<br/><br/><br/>*terms and conditions apply see website for details<br/><br/>KEEP IN MIND THE EXAMPLES I AM UPLOADING ARE SIMPLY TO SHOW YOU THAT THEY CONTAIN THE "COMPLIMENTS OF" AND "EXCLUSIVELY FOR" ELEMENTS. THESE MUST BE INCLUDED IN NEW DESIGN. PLEASE ONLY USE THE CONTENT I PROVIDED IN BRIEF, DONT USE CONTENT FROM EXAMPLES.

Target Market(s)

CONSUMERS THAT HAVE BEEN REWARDED WITH A VACATION CERTIFICATE FOR DOING BUSINESS WITH A COMPANY.

COMPANIES USE THESE AS MARKETING INCENTIVES TO ATTRACT MORE CUSTOMERS AND TO REWARD LOYALTY, ETC.

Industry/Entity Type

Travel Industry

Colors

Designer to choose colors to be used in the design.

Requirements
Must have
• I need to create a beautiful flyer 8.5 x 11 PDF format flyer design.
• Instructions:
• The flyer will really be a gift voucher for a las vegas vacation getaway. So must have a Las Vegas Theme exciting fun
• The voucher should have two modules that will be editable.
• Must have a "Compliments Of" area and also must have an "Exclusively For" area
• Keep in mind that this flyer will be printed so keep that in mind :)
• Here the is the content for the vacation voucher:
• There is no doubt that Las Vegas is one of the hottest travel destinations around the world. In fact, some people would even go as far as
• saying that perhaps it is THE hottest place to visit. Enjoy up to 4 nights of resort/casino accommodations in exciting Las Vegas, NV. Millions of people travel to this exciting city each year to enjoy its thrills. Thanks to the business you received this certificate from, now you can enjoy exciting Las Vegas, NV too!
• Features:
• *Travel 7 Days A Week
• *Stay Your Choice Of Nights (1-4 Nights)
• *Good For Two Adults & Two Children
• *Pay Just The Taxes & Fees
• *Multiple Travel Date Requests Allowed
• *Fully Transferable To Another Person
• *Just A 30 Days Advance Notice Required
• *You Will Have 12 Months To Complete Travel After Redemption
• HOW CAN WE DO THIS?
• We contract with the world leading hotel chains and resorts to help them fill their otherwise empty rooms.
• We help fill empty rooms which the hotels, resorts and cruise lines turn into additional revenue from other areas of their property and future bookings.
• Hotels rarely experience full occupancy, yet they remain open, providing rooms and services at fixed costs. So when hotels give out their rooms by partnering with marketing companies like us, they might miss out on the room fee, but they already didn't have that in the first place, at least now they have the opportunity to gain a customer for their in-house restaurants, room service, their casinos, an extra day stay, future bookings, etc.
• VIEW ALL THE DETAILS OF THIS SPECIAL OFFER AND REDEEM ONLINE AT
• WWW.QOTAVERNIX.COM
• Certificate ID # 47261-38157
• Expires 02/29/2020
• *terms and conditions apply see website for details
• KEEP IN MIND THE EXAMPLES I AM UPLOADING ARE SIMPLY TO SHOW YOU THAT THEY CONTAIN THE "COMPLIMENTS OF" AND "EXCLUSIVELY FOR" ELEMENTS. THESE MUST BE INCLUDED IN NEW DESIGN. PLEASE ONLY USE THE CONTENT I PROVIDED IN BRIEF, DONT USE CONTENT FROM EXAMPLES.
Nice to have
• EXCITING LAS VEGAS IMAGES THAT MAKE SOMEONE WANT TO GO THERE

```html
<!DOCTYPE html>
<html lang="en">
<head>
<meta charset="utf-8">
<title>Las Vegas Vacation Getaway Certificate</title>
<link href="https://fonts.googleapis.com/css2?family=Bebas+Neue&family=Oswald:wght@400&family=Montserrat:wght@400;600&display=swap" rel="stylesheet">
<style>
  :root {
    --stage: #2d2d2d;
    --navy: #1f2433;
    --blue: #10a8e6;
    --sky: #4fc3ea;
    --white: #ffffff;
    --ink: #1b1b1b;
    --grey: #7b7f88;
  }
  * { margin: 0; padding: 0; box-sizing: border-box; }
  html, body { width: 1200px; height: 1200px; overflow: hidden; background: var(--stage); }
  body { position: relative; font-family: "Montserrat", sans-serif; }

  .page {
    position: absolute; top: 240px; width: 680px; height: 950px;
    background: var(--white); overflow: hidden;
    transform: scale(0.8); transform-origin: 0 0;
    box-shadow: 0 8px 24px rgba(0,0,0,.5);
  }
  .page--front { left: 38px; }
  .page--back { left: 623px; }
  .page svg.shapes { position: absolute; inset: 0; width: 680px; height: 950px; }

  .title { position: absolute; left: 22px; top: 236px; color: var(--white); font-family: "Bebas Neue", sans-serif; font-weight: 400; line-height: 1; }
  .title__main { font-size: 80px; letter-spacing: 2px; display: block; }
  .title__sub { font-size: 48px; letter-spacing: 1px; display: block; margin-top: 4px; }
  .title-rule { position: absolute; left: 0; top: 376px; width: 315px; height: 3px; background: var(--white); }
  .intro { position: absolute; left: 21px; top: 390px; width: 290px; color: var(--white); font-size: 13.4px; line-height: 16px; }

  .module { position: absolute; top: 624px; width: 308px; height: 290px; border: 3px solid var(--blue); border-radius: 22px; overflow: hidden; }
  .module--from { left: 22px; }
  .module--for { left: 351px; }
  .module__head { height: 60px; background: var(--navy); color: var(--blue); font-family: "Oswald", sans-serif; font-weight: 400; font-size: 29px; display: flex; align-items: center; justify-content: center; border-radius: 0 0 22px 22px; }

  .band { position: absolute; left: 0; right: 0; }
  .band--blue { top: 935px; height: 8px; background: var(--blue); }
  .band--dark { top: 943px; height: 7px; background: var(--navy); }
  .page--back .band--dark { top: 933px; height: 17px; }

  .pill { position: absolute; right: 0; background: var(--navy); color: var(--blue); font-family: "Bebas Neue", sans-serif; border-radius: 30px 0 0 30px; padding-right: 24px; text-align: right; }
  .pill--features { top: 48px; width: 212px; height: 50px; font-size: 48px; line-height: 54px; }
  .pill--how { top: 450px; width: 343px; height: 42px; font-size: 42px; line-height: 46px; }

  .features { position: absolute; right: 22px; top: 104px; list-style: none; text-align: right; color: var(--ink); font-size: 15.5px; line-height: 19px; }
  .features li { margin-bottom: 14px; padding-right: 24px; position: relative; }
  .features li::after { content: "\2713"; position: absolute; right: 0; top: 0; color: var(--blue); font-weight: 600; }
  .features b { font-weight: 600; }

  .reasons { position: absolute; right: 24px; top: 510px; width: 380px; list-style: none; text-align: right; color: var(--ink); font-size: 13.4px; line-height: 16px; }
  .reasons li { padding-right: 16px; position: relative; margin-bottom: 10px; }
  .reasons li::after { content: ""; position: absolute; right: 0; top: 5px; width: 7px; height: 7px; border-radius: 50%; background: var(--navy); }

  .photo { position: absolute; left: 21px; width: 247px; height: 166px; }
  .photo--cocktail { top: 390px; background: linear-gradient(135deg, #0c2a6b, #c5302b 55%, #f2b84a); }
  .photo--friends { top: 574px; background: linear-gradient(160deg, #6fb4e6, #d9a37f 55%, #5b4a6b); }
  .photo--canal { top: 767px; background: linear-gradient(180deg, #3a5370, #c97a2e 50%, #23414a); }

  .redeem { position: absolute; left: 268px; right: 0; top: 788px; height: 145px; background: var(--blue); color: var(--white); text-align: right; padding: 10px 42px 0 0; font-size: 13.4px; font-weight: 600; line-height: 16px; }
  .redeem__url { margin-top: 10px; font-size: 14px; }
  .redeem__id { margin-top: 14px; }
  .redeem__exp { margin-top: 4px; }
  .redeem__date { background: var(--navy); border-radius: 10px; padding: 1px 6px; }
  .redeem__terms { margin-top: 8px; font-weight: 400; margin-right: -12px; }
</style>
</head>
<body>

<section class="page page--front">
  <svg class="shapes" viewBox="0 0 680 950">
    <defs>
      <radialGradient id="cityNight" cx="55%" cy="55%" r="60%">
        <stop offset="0" stop-color="#c58a48"/>
        <stop offset="0.45" stop-color="#3b3f66"/>
        <stop offset="1" stop-color="#0d1226"/>
      </radialGradient>
      <linearGradient id="signSky" x1="0" y1="0" x2="0" y2="1">
        <stop offset="0" stop-color="#2d4e86"/>
        <stop offset="0.6" stop-color="#e9a96a"/>
        <stop offset="1" stop-color="#3a3550"/>
      </linearGradient>
    </defs>
    <circle cx="500" cy="230" r="342" fill="none" stroke="#10a8e6" stroke-width="7"/>
    <circle cx="500" cy="230" r="330" fill="url(#cityNight)" role="img" aria-label="Night view of the Las Vegas Strip with lit fountains and casino towers"/>
    <circle cx="145" cy="364" r="224" fill="#1f2433"/>
    <circle cx="174" cy="125" r="70" fill="#4fc3ea" opacity="0.85"/>
    <circle cx="496" cy="510" r="96" fill="#10a8e6"/>
    <circle cx="496" cy="510" r="89" fill="#ffffff"/>
    <circle cx="496" cy="510" r="84" fill="url(#signSky)" role="img" aria-label="Welcome to Las Vegas roadside sign at sunset"/>
  </svg>

  <h1 class="title"><span class="title__main">LAS VEGAS</span><span class="title__sub">VACATION GETAWAY</span></h1>
  <div class="title-rule"></div>
  <p class="intro">Las Vegas is one of the hottest travel destinations around the world.THE hottest place to visit. Enjoy up to 4 nights of resort/casino accommodations in exciting Las Vegas, NV. Millions of people travel to this exciting city each year to enjoy its thrills. Thanks to the business you received this certificate from, now you can enjoy exciting Las Vegas, NV too!</p>

  <div class="module module--from"><div class="module__head">Compliments Of</div></div>
  <div class="module module--for"><div class="module__head">Exclusively For</div></div>

  <div class="band band--blue"></div>
  <div class="band band--dark"></div>
</section>

<section class="page page--back">
  <svg class="shapes" viewBox="0 0 680 950">
    <defs>
      <linearGradient id="arcade" x1="0" y1="0" x2="1" y2="1">
        <stop offset="0" stop-color="#c94a3a"/>
        <stop offset="0.5" stop-color="#6fc3a0"/>
        <stop offset="1" stop-color="#2b3a5a"/>
      </linearGradient>
    </defs>
    <circle cx="0" cy="-32" r="412" fill="#10a8e6"/>
    <circle cx="0" cy="-32" r="401" fill="#ffffff"/>
    <circle cx="0" cy="-32" r="395" fill="url(#arcade)" role="img" aria-label="Neon-lit covered street canopy in downtown Las Vegas with crowds below"/>
    <circle cx="191" cy="322" r="40" fill="#7b7f88" opacity="0.85"/>
  </svg>

  <div class="pill pill--features">FEATURES</div>
  <ul class="features">
    <li>Travel 7 Days A Week</li>
    <li>Stay Your Choice Of Nights<br><b>(1-4 Nights)</b></li>
    <li>Good For <b>Two Adults &amp;<br>Two Children</b></li>
    <li>Pay Just The Taxes &amp; Fees</li>
    <li>Multiple Travel Date Requests Allowed</li>
    <li>Fully Transferable To Another Person</li>
    <li>Just A <b>30 Days</b> Advance Notice Required</li>
    <li>You Will Have <b>12 Months</b> To Complete</li>
    <li>Travel After Redemption</li>
  </ul>

  <div class="pill pill--how">HOW CAN WE DO THIS?</div>
  <ul class="reasons">
    <li>We contract with the world leading hotel chains and resorts to help them fill their otherwise empty rooms.</li>
    <li>We help fill empty rooms which the hotels,resorts and cruise lines turn into additional revenue from other areas of their property and future bookings.</li>
    <li>Hotels rarely experience full occupancy, yet they remain open, providing rooms and services at fixed costs. So when hotels give out their rooms by partnering with marketing companies like us, they might miss out on the room fee, but they already didn't have that in the first place, at least now they have the opportunity to gain a customer for their in-house restaurants, room service, their casinos, an extra day stay, future bookings, etc.</li>
  </ul>

  <div class="photo photo--cocktail" role="img" aria-label="Cocktail glass with red dice"></div>
  <div class="photo photo--friends" role="img" aria-label="Group of friends on holiday in Las Vegas"></div>
  <div class="photo photo--canal" role="img" aria-label="Gondola on an indoor canal at a resort"></div>

  <div class="redeem">
    <p>VIEW ALL THE DETAILS OF THIS SPECIAL OFFER<br>AND REDEEM ONLINE AT</p>
    <p class="redeem__url">WWW.QOTAVERNIX.COM</p>
    <p class="redeem__id">Certificate ID # 47261-38157</p>
    <p class="redeem__exp">Expires <span class="redeem__date">02/29/2020</span></p>
    <p class="redeem__terms">*terms and conditions apply see website for details</p>
  </div>

  <div class="band band--dark"></div>
</section>

</body>
</html>
```